Business Card for Coastal Tundrabridge Advisory

We need a business card for Coastal Tundrabridge Advisory. The company website address is provided below. The company logo is attached. We provide specialized permafrost services to the mining, transportation, and oil & gas industries. The card should be prepared for:
Matthias Korhonen, PhD.
Coastal Tundrabridge Advisory
PO Box 418259
Quillwater, Alaska 99642
Direct: +1-907-555-0143
Email: mkorhonen@tundrabridgeadvisory.example
Website: www.coastaltundrabridgeadvisory.example

```html
<!DOCTYPE html>
<html lang="en">
<head>
<meta charset="utf-8">
<title>Coastal Tundrabridge Advisory – Business Card</title>
<link href="https://fonts.googleapis.com/css2?family=Montserrat:wght@400;700&display=swap" rel="stylesheet">
<style>
  :root {
    --backdrop: #7a6248;
    --card-front: #ffffff;
    --card-back: #2a2a2a;
    --ink: #16191d;
    --ink-soft: #2b2e33;
    --back-wordmark: #cfcfcf;
  }
  * { margin: 0; padding: 0; box-sizing: border-box; }
  html, body {
    width: 900px; height: 1200px; overflow: hidden;
    background: var(--backdrop);
    font-family: "Montserrat", sans-serif;
  }
  .stage { position: relative; width: 900px; height: 1200px; }
  .card {
    position: absolute; left: 80px; width: 742px; height: 440px;
    border-radius: 34px;
    box-shadow: 4px 6px 10px rgba(0,0,0,0.45);
  }
  .card--front { top: 132px; background: var(--card-front); color: var(--ink); }
  .card--back { top: 638px; height: 442px; background: var(--card-back); }

  .wordmark {
    position: absolute; left: 45px; top: 80px;
    font-weight: 700; font-size: 30px; letter-spacing: 0.5px;
    color: var(--ink); white-space: nowrap;
  }
  .wordmark--back {
    left: 0; right: 0; top: 190px; text-align: center;
    font-size: 40px; color: var(--back-wordmark);
  }

  .person { position: absolute; left: 38px; top: 266px; }
  .person__name { font-weight: 700; font-size: 27px; line-height: 1.2; color: var(--ink); }
  .person__role { font-size: 16px; color: var(--ink-soft); margin-top: 1px; }

  .rule {
    position: absolute; left: 38px; top: 326px; width: 671px;
    height: 1.5px; background: var(--ink);
  }

  .contacts { position: absolute; left: 40px; top: 343px; list-style: none; }
  .contacts li {
    display: flex; align-items: center; gap: 9px;
    font-size: 16px; line-height: 22.5px; color: var(--ink-soft);
  }
  .contacts svg { width: 14px; height: 14px; fill: var(--ink); flex: none; }

  .address {
    position: absolute; left: 467px; top: 372px;
    border-left: 1.5px solid var(--ink); padding-left: 17px;
    font-size: 16px; line-height: 20px; color: var(--ink-soft);
  }
</style>
</head>
<body>
<div class="stage">
  <section class="card card--front">
    <div class="wordmark">Coastal Tundrabridge Advisory</div>

    <div class="person">
      <div class="person__name">Matthias Korhonen, PhD.</div>
      <div class="person__role">CEO &amp; Founder</div>
    </div>

    <div class="rule"></div>

    <ul class="contacts">
      <li>
        <svg viewBox="0 0 16 16" aria-hidden="true"><path d="M2 6c0-2 2-3 6-3s6 1 6 3v1h-3V6H5v1H2zM4 8h8l2 5H2z"/></svg>
        +1-907-555-0143
      </li>
      <li>
        <svg viewBox="0 0 16 16" aria-hidden="true"><path d="M1 4h14v1L8 9 1 5zM1 6.5l7 4 7-4V12H1z"/></svg>
        mkorhonen@tundrabridgeadvisory.example
      </li>
      <li>
        <svg viewBox="0 0 16 16" aria-hidden="true"><circle cx="8" cy="8" r="6.5"/><path d="M5 4c2 1 1 3 3 3s1 3 3 3" stroke="#fff" stroke-width="1.4" fill="none"/></svg>
        www.coastaltundrabridgeadvisory.example
      </li>
    </ul>

    <div class="address">
      PO Box 418259<br>
      Quillwater, Alaska 99642
    </div>
  </section>

  <section class="card card--back">
    <div class="wordmark wordmark--back">Coastal Tundrabridge Advisory</div>
  </section>
</div>
</body>
</html>
```